Simple Logo Design for Semi-Clear Plastic Frosted Card stock

Create a business card on frosted plastic. compliment existing logo elements with a tree trunk, roots, or seed at the lower half and the full logo both on the front.

Contact information will go on a solid portion of the back of this design since this card stock is semi-transparent.

It is important to consider this plastic card stock medium in your design. I found helpful tips and guides listed at vellaprint-sample.net: be careful to understand ink printed on plastic cards cannot have too much of a consistent print area or risks peeling and fine lines can easily scratch off.
Updates

2" x 3.5" 20PT Clear Plastic Business cards with Round corners Please get info or templates here: https://www.vellaprint-sample.net/product-detail/2-x-35-20pt-clear-plastic-business-cards-with-round-corners

Target Market(s)

Not for profit- religion

Industry/Entity Type

Business

Must include complementary elements to the existing logo

Font styles to use
Decorative

Colors
000000

Requirements
Must have
• Elements of community, nature and oneness. Such as: seed, roots, tree trunk, etc.
• Three lines of space on the back for Name, Title, Phone Number.
Nice to have
• I like a light use of decorative elements
Should not have
• No eyes, from faces or animals.

```html
<!DOCTYPE html>
<html lang="en">
<head>
<meta charset="utf-8">
<title>Trueroot Circle – Frosted Business Card</title>
<link rel="stylesheet" href="https://fonts.googleapis.com/css2?family=Mulish:wght@400;600;800&display=swap">
<style>
  :root {
    --backdrop: #e8e5df;
    --teal-deep: #0c3b3a;
    --teal-mid: #1f5a55;
    --frost: #e4ebea;
    --frost-edge: #cdd8d6;
    --ring-green: #2f6b1f;
    --ink-dark: #143c34;
    --ink-light: #e6efec;
  }
  * { margin: 0; padding: 0; box-sizing: border-box; }
  html, body {
    width: 1200px;
    height: 685px;
    overflow: hidden;
    background: var(--backdrop);
    font-family: "Mulish", sans-serif;
  }
  .canvas {
    position: relative;
    width: 1200px;
    height: 685px;
  }
  .card {
    position: absolute;
    top: 224px;
    width: 455px;
    height: 260px;
    border-radius: 16px;
    overflow: hidden;
    box-shadow: 0 6px 18px rgba(0, 0, 0, 0.12);
  }
  .card--front { left: 124px; }
  .card--back { left: 602px; }
  .card__art {
    position: absolute;
    inset: 0;
    width: 100%;
    height: 100%;
  }
  .contact {
    position: absolute;
    left: 30px;
    top: 96px;
    color: var(--ink-light);
  }
  .contact__name {
    font-size: 16px;
    font-weight: 600;
    letter-spacing: 0.04em;
    text-transform: uppercase;
  }
  .contact__title {
    font-size: 13px;
    font-weight: 400;
    letter-spacing: 0.04em;
    text-transform: uppercase;
    opacity: 0.85;
    margin-top: 4px;
  }
  .contact__phone {
    font-size: 14px;
    font-weight: 400;
    letter-spacing: 0.03em;
    margin-top: 12px;
    opacity: 0.9;
  }
  .brand {
    position: absolute;
    display: flex;
    align-items: center;
    gap: 7px;
    font-size: 17px;
    font-weight: 800;
    letter-spacing: 0.03em;
    text-transform: uppercase;
    white-space: nowrap;
  }
  .brand__dot {
    width: 12px;
    height: 12px;
    border-radius: 50%;
    background: currentColor;
  }
  .card--front .brand {
    left: 236px;
    top: 146px;
    color: var(--ink-dark);
  }
  .card--back .brand {
    left: 40px;
    top: 146px;
    color: var(--ink-dark);
    opacity: 0.55;
    transform: scaleX(-1);
  }
</style>
</head>
<body>
<main class="canvas">
  <section class="card card--front" aria-label="Card front">
    <svg class="card__art" viewBox="0 0 455 260" aria-hidden="true">
      <defs>
        <linearGradient id="frontTeal" x1="0" y1="0" x2="1" y2="1">
          <stop offset="0" stop-color="#2a625c"/>
          <stop offset="0.6" stop-color="#0f403e"/>
          <stop offset="1" stop-color="#0a3634"/>
        </linearGradient>
        <radialGradient id="frontFrost" cx="0.45" cy="0.4" r="0.7">
          <stop offset="0" stop-color="#f3f7f7"/>
          <stop offset="1" stop-color="#d3dcda"/>
        </radialGradient>
      </defs>
      <rect width="455" height="260" fill="url(#frontTeal)"/>
      <circle cx="327" cy="130" r="136" fill="url(#frontFrost)"/>
      <circle cx="327" cy="130" r="136" fill="none" stroke="var(--ring-green)" stroke-width="2.5"/>
    </svg>
    <div class="brand"><span class="brand__dot"></span>Trueroot Circle</div>
  </section>

  <section class="card card--back" aria-label="Card back">
    <svg class="card__art" viewBox="0 0 455 260" aria-hidden="true">
      <defs>
        <linearGradient id="backTeal" x1="0" y1="0" x2="1" y2="1">
          <stop offset="0" stop-color="#135552"/>
          <stop offset="1" stop-color="#0a3937"/>
        </linearGradient>
        <radialGradient id="backFrost" cx="0.5" cy="0.45" r="0.7">
          <stop offset="0" stop-color="#e6ebe9"/>
          <stop offset="1" stop-color="#ccd5d2"/>
        </radialGradient>
      </defs>
      <rect width="455" height="260" fill="url(#backTeal)"/>
      <rect width="133" height="260" fill="url(#backFrost)"/>
      <circle cx="133" cy="130" r="133" fill="url(#backFrost)"/>
      <circle cx="133" cy="130" r="133" fill="none" stroke="var(--ring-green)" stroke-width="2.5"/>
    </svg>
    <div class="brand"><span class="brand__dot"></span>Trueroot Circle</div>
  </section>

  <section class="card card--front-info" aria-hidden="true" style="display:none"></section>
</main>
<style>
  /* contact block sits on the solid teal of the front card */
</style>
<div class="contact" style="left:154px; top:320px;">
  <p class="contact__name">Alan Mercer</p>
  <p class="contact__title">President</p>
  <p class="contact__phone">555 0142 7788</p>
</div>
</body>
</html>
```